Menu Redesign - Upscale Restaurant

We are looking to have our lunch and dinner menus redesigned. We are looking to elevate the signs some, no emojis. We want a clean but elevated look, please refer to Marlowe’s Dining Collective food menu and Vesper Tavola’s beverage menu. The company we’ve been using presented us with the attached menu / it’s filled with spelling and grammar errors.

Industry/Entity Type

Restaurant - Hospitality

```html
<!DOCTYPE html>
<html lang="en">
<head>
<meta charset="utf-8">
<title>Miss Della's Creole House — Lunch &amp; Drinks Menu</title>
<link href="https://fonts.googleapis.com/css2?family=Playfair+Display:wght@400;700&family=Poppins:wght@400;500;600&display=swap" rel="stylesheet">
<style>
:root{
  --backdrop:#8a8a8a;
  --paper:#ece6dc;
  --red:#c4212f;
  --gold:#c39a57;
  --gold-soft:#d9bf94;
  --ink:#1d1b19;
  --muted:#4a4540;
}
*{box-sizing:border-box;margin:0;padding:0}
html,body{width:1200px;height:2734px;overflow:hidden;background:var(--backdrop)}
body{position:relative;font-family:"Poppins",sans-serif;color:var(--ink)}
.page{position:absolute;left:190px;width:820px;height:1160px;background:var(--paper);box-shadow:0 6px 18px rgba(0,0,0,.28)}
.page--lunch{top:170px}
.page--drinks{top:1405px}
.serif{font-family:"Playfair Display",serif}

/* header */
.brand{position:absolute;left:55px;top:60px;width:250px;height:110px;display:flex;align-items:center;gap:10px}
.brand__dot{width:14px;height:14px;border-radius:50%;background:var(--red);flex:none}
.brand__name{font-family:"Playfair Display",serif;font-weight:700;font-size:36px;color:var(--red);line-height:1}
.header__rule{position:absolute;left:367px;top:50px;width:1px;height:90px;background:#c9b9a6}
.hours{position:absolute;left:441px;top:38px;font-family:"Playfair Display",serif;line-height:1.15}
.hours h3{color:var(--red);font-weight:700;font-size:22px;letter-spacing:.3px}
.hours p{font-size:16px;color:var(--ink)}
.hours p.small{font-size:14px;margin-bottom:6px}
.band{position:absolute;left:0;width:820px;border-top:1.5px solid var(--red);border-bottom:1px solid var(--red);height:5px}
.band__title{position:absolute;left:50%;transform:translateX(-50%);background:var(--paper);padding:0 6px;color:var(--red);font-family:"Playfair Display",serif;font-weight:700;font-size:28px;line-height:1}

/* section headings */
.heading{font-family:"Playfair Display",serif;font-weight:700;color:var(--red);font-size:25px;line-height:1.1;letter-spacing:.3px}
.flourish{display:block;height:8px;margin:4px 0 0;border-radius:4px;background:linear-gradient(90deg,transparent,var(--muted) 15%,var(--muted) 85%,transparent);opacity:.55}

/* items */
.col{position:absolute;display:flex;flex-direction:column}
.list{display:flex;flex-direction:column;justify-content:space-between;flex:1}
.item .row{display:flex;align-items:flex-end;font-weight:600;font-size:11.5px;line-height:1.2}
.item .lead{flex:1;border-bottom:1px solid var(--ink);margin:0 3px 3px;min-width:8px}
.item .price{font-size:11.5px}
.item .price sup,.price sup{font-size:7px}
.item .desc{font-size:5.6px;line-height:1.35;color:var(--muted);margin-top:2px;max-width:96%}

/* framed boxes */
.frame{position:absolute;border:2px solid var(--gold);border-radius:10px}
.frame .heading{text-align:center}
.note{position:absolute;background:var(--gold-soft);border-radius:8px;font-size:7.5px;line-height:1.3;color:var(--ink)}
.note b{font-weight:600;font-size:9px}

/* sides */
.sides{position:absolute;left:45px;top:955px;width:730px;height:110px;border:1.5px solid var(--gold);border-radius:14px;display:grid;grid-template-columns:1fr 1fr 1fr}
.sides__col{padding:20px 0 0 58px;font-size:9.5px;font-weight:600;line-height:1.7;border-right:1px solid var(--gold)}
.sides__col:last-child{border-right:0;padding-left:50px}
.sides__col sup{color:var(--red);font-size:7px}
.footer{position:absolute;left:0;width:820px;text-align:center;font-size:9px;line-height:1.35}
.footer b{font-weight:600}

.ornament{position:absolute;background:linear-gradient(180deg,var(--gold),#b88b45);opacity:.85}
</style>
</head>
<body>

<!-- LUNCH PAGE -->
<section class="page page--lunch">
  <div class="brand"><span class="brand__dot"></span><span class="brand__name">Miss Della's</span></div>
  <div class="header__rule"></div>
  <div class="hours">
    <h3>HAPPY HOUR FOOD &amp; DRINKS</h3>
    <p>MONDAY TO FRIDAY 3:00PM-6:00PM</p>
    <p class="small">Bar seats and high top tables by bar ONLY</p>
    <h3>BRUNCH</h3>
    <p>SATURDAY &amp; SUNDAY 10:00AM-4:00PM</p>
  </div>
  <div class="band" style="top:172px"></div>
  <div class="band__title" style="top:163px">LUNCH MENU</div>

  <div class="col" style="left:45px;top:198px;width:196px;height:712px">
    <h2 class="heading">SMALL PLATES</h2>
    <span class="flourish" role="img" aria-label="Scroll flourish divider"></span>
    <div class="list" style="margin-top:6px">
      <div class="item"><div class="row">FRIED DEVIL EGGS<span class="lead"></span><span class="price"><sup>$</sup>13</span></div><p class="desc">Sweet relish deviled eggs topped with lump crab or shrimp for an upcharge.</p></div>
      <div class="item"><div class="row">FRIED GREEN TOMATOES<span class="lead"></span><span class="price"><sup>$</sup>13</span></div><p class="desc">Sliced green tomatoes in house breading, panko crumb. Add lump crab +$6.</p></div>
      <div class="item"><div class="row">SPINACH DIP<span class="lead"></span><span class="price"><sup>$</sup>14</span></div><p class="desc">Chopped spinach in four cheese blend with fresh tortilla chips.</p></div>
      <div class="item"><div class="row">BAYOU EGG ROLLS<span class="lead"></span><span class="price"><sup>$</sup>15</span></div><p class="desc">Diced chicken, peppers and cheese in egg roll, remoulade dipping.</p></div>
      <div class="item"><div class="row">HOT HONEY SALMON BITES<span class="lead"></span><span class="price"><sup>$</sup>15</span></div><p class="desc">Crispy salmon bites tossed in hot honey glaze, choice of topping.</p></div>
      <div class="item"><div class="row">CUP OF GUMBO<span class="lead"></span><span class="price"><sup>$</sup>15</span></div><p class="desc">Andouille, shrimp, chicken slow cooked in cajun broth with rice.</p></div>
      <div class="item"><div class="row">CREOLE WINGS<span class="lead"></span><span class="price"><sup>$</sup>16</span></div><p class="desc">Fried crispy wings tossed in your choice of signature sauce.</p></div>
      <div class="item"><div class="row">SEAFOOD EGG ROLLS<span class="lead"></span><span class="price"><sup>$</sup>16</span></div><p class="desc">Chopped shrimp, crab and cheese in egg roll, remoulade dipping.</p></div>
      <div class="item"><div class="row">VOODOO SHRIMP<span class="lead"></span><span class="price"><sup>$</sup>16</span></div><p class="desc">Fried shrimp tossed in voodoo sauce with jalapenos and blue cheese.</p></div>
      <div class="item"><div class="row">NEW ORLEANS SHRIMP<span class="lead"></span><span class="price"><sup>$</sup>16</span></div><p class="desc">Creamy garlic cajun sauteed shrimp served with toasted bread.</p></div>
      <div class="item"><div class="row">RAW OYSTER<span class="lead"></span><span class="price"><sup>$</sup>16</span></div><p class="desc">Fresh shucked oysters over ice with lemon, horseradish and mignonette.</p></div>
      <div class="item"><div class="row">STEAK &amp; CHEESE ROLLS<span class="lead"></span><span class="price"><sup>$</sup>16</span></div><p class="desc">Shaved steak, grilled onions, peppers, cheese, chipotle mayo.</p></div>
      <div class="item"><div class="row">CHARGRILLED OYSTERS<span class="lead"></span><span class="price"><sup>$</sup>17</span></div><p class="desc">Fresh oysters grilled with cajun garlic butter and four cheese blend.</p></div>
      <div class="item"><div class="row">ROCKEFELLER OYSTERS<span class="lead"></span><span class="price"><sup>$</sup>18</span></div><p class="desc">Fresh oysters stuffed with creamy spinach and cheese.</p></div>
      <div class="item"><div class="row">SEAFOOD BASKET<span class="lead"></span><span class="price"><sup>$</sup>18</span></div><p class="desc">Battered catfish or fried shrimp with season fries.</p></div>
      <div class="item"><div class="row">STUFFED SHRIMP<span class="lead"></span><span class="price"><sup>$</sup>18</span></div><p class="desc">Shrimp stuffed with lump crab, fried golden over jalapeño corn succotash.</p></div>
      <div class="item"><div class="row">JAMBALAYA OYSTERS<span class="lead"></span><span class="price"><sup>$</sup>22</span></div><p class="desc">Fresh oysters stuffed with creamy cajun shrimp and crab.</p></div>
      <div class="item"><div class="row">MAKE IT A PLATTER<span class="lead"></span><span class="price"><sup>$</sup>30</span></div><p class="desc">(Serves 3)<br>Mix 3 of your favorite starters.<br>(Each seafood starter added to platter is upcharged)</p></div>
    </div>
  </div>

  <div class="frame" style="left:285px;top:195px;width:230px;height:605px;padding:12px 18px 18px">
    <h2 class="heading">LUNCH<br>FAVORITES</h2>
    <span class="flourish" role="img" aria-label="Scroll flourish divider" style="width:120px;margin:4px auto 0"></span>
    <p style="color:var(--red);font-size:9px;text-align:center;line-height:1.4;margin-top:12px">Two For You - the perfect lunch pair<br>Any Po' Boy + Pick any Hurricane — $22</p>
    <div class="list" style="height:455px;margin-top:12px">
      <div class="item"><div class="row">SHRIMP PO' BOY<span class="lead"></span><span class="price"><sup>$</sup>16</span></div><p class="desc">Fried or blackened shrimp with lettuce, tomatoes, pickles, remoulade. Fries or salad.</p></div>
      <div class="item"><div class="row">CHICKEN CHEESESTEAK<br>PO' BOY<span class="lead"></span><span class="price"><sup>$</sup>16</span></div><p class="desc">Cajun diced chicken, peppers, onions, melted cheese, lettuce, tomatoes, pickles. Add bacon +$2.</p></div>
      <div class="item"><div class="row">HOT HONEY SALMON PO' BOY<span class="lead"></span><span class="price"><sup>$</sup>16</span></div><p class="desc">Fried salmon in hot honey with lettuce, tomatoes, pickles. Fries or salad.</p></div>
      <div class="item"><div class="row">CATFISH PO' BOY<span class="lead"></span><span class="price"><sup>$</sup>16</span></div><p class="desc">Fried or blackened catfish with lettuce, tomatoes, pickles, remoulade. Fries or salad.</p></div>
      <div class="item"><div class="row">STEAK &amp; CHEESE PO' BOY<span class="lead"></span><span class="price"><sup>$</sup>16</span></div><p class="desc">Shaved cajun steak, peppers, onions, melted cheese, lettuce, tomatoes. Add bacon +$2.</p></div>
      <div class="item"><div class="row">CHICKEN CAESAR SALAD<span class="lead"></span><span class="price"><sup>$</sup>17</span></div><p class="desc">Grilled chicken, romaine, parmesan, croutons, house caesar.</p></div>
      <div class="item"><div class="row">ULTIMATE CHEESEBURGER<span class="lead"></span><span class="price"><sup>$</sup>17</span></div><p class="desc">Beef patty, white cheddar, lettuce, tomato, served with fries.</p></div>
      <div class="item"><div class="row">HONEY CARIBBEAN SALMON<span class="lead"></span><span class="price"><sup>$</sup>18</span></div><p class="desc">Field greens, corn, tomatoes, cucumbers, red onions, buttermilk ranch dressing.</p></div>
      <div class="item"><div class="row">BLACKENED CHICKEN ALFREDO<span class="lead"></span><span class="price"><sup>$</sup>18</span></div><p class="desc">Blackened chicken, cajun cream sauce, fettuccine, parmesan cheese.</p></div>
      <div class="item"><div class="row">MISS DELLA'S FRIED CHICKEN<span class="lead"></span><span class="price"><sup>$</sup>18</span></div><p class="desc">Quarter chicken in southern seasonings, fried golden with one side.</p></div>
      <div class="item"><div class="row">GUMBO W/ CORNBREAD<span class="lead"></span><span class="price"><sup>$</sup>18</span></div><p class="desc">Rich roux with chicken, andouille, shrimp and scallion rice. Add crab leg +$10.</p></div>
    </div>
  </div>
  <div class="note" style="left:278px;top:818px;width:182px;height:34px;padding:4px 10px"><b>Add Protein:</b><br>Shrimp +7, Salmon +12, Blackened Chicken +10, Steak +15</div>
  <p style="position:absolute;left:278px;top:858px;width:240px;font-size:7.5px;line-height:1.4"><b style="font-weight:600">Dressing Options:</b> Honey Mustard, Balsamic Vinaigrette, Ranch, Caesar, Blue Cheese</p>

  <div class="col" style="left:560px;top:198px;width:195px;height:680px">
    <h2 class="heading">ENTREES</h2>
    <span class="flourish" role="img" aria-label="Scroll flourish divider" style="width:120px"></span>
    <div class="list" style="margin-top:6px">
      <div class="item"><div class="row">CAJUN SALMON<span class="lead"></span><span class="price"><sup>$</sup>13</span></div><p class="desc">Pan-seared salmon topped with creamy creole sauce, two sides.</p></div>
      <div class="item"><div class="row">MISS DELLA'S FRIED CHICKEN<span class="lead"></span><span class="price"><sup>$</sup>23</span></div><p class="desc">Half chicken in southern seasonings, fried golden, two sides.</p></div>
      <div class="item"><div class="row">GUMBO W/ CORNBREAD<span class="lead"></span><span class="price"><sup>$</sup>25</span></div><p class="desc">Rich roux with chicken, andouille, fresh shrimp, scallion rice. Add crab leg +$10.</p></div>
      <div class="item"><div class="row">FRIED CATFISH<span class="lead"></span><span class="price"><sup>$</sup>25</span></div><p class="desc">Catfish fried golden or blackened with two sides.</p></div>
      <div class="item"><div class="row">PORK CHOPS<span class="lead"></span><span class="price"><sup>$</sup>25</span></div><p class="desc">Fried or grilled chops smothered in southern gravy, two sides.</p></div>
      <div class="item"><div class="row">BAYOU PASTA<span class="lead"></span><span class="price"><sup>$</sup>26</span></div><p class="desc">House cream sauce, peppers, tomatoes, onions, linguine, blackened chicken.</p></div>
      <div class="item"><div class="row">JAMBALAYA PASTA<span class="lead"></span><span class="price"><sup>$</sup>27</span></div><p class="desc">Shrimp, chicken, andouille, veggies in cajun cream sauce.</p></div>
      <div class="item"><div class="row">CREOLE HERB CHICKEN<span class="lead"></span><span class="price"><sup>$</sup>28</span></div><p class="desc">Herb seasoned half chicken roasted tender, creole sauce, two sides.</p></div>
      <div class="item"><div class="row">CATFISH &amp; GRITS<span class="lead"></span><span class="price"><sup>$</sup>28</span></div><p class="desc">Blackened or fried catfish over cheddar grits, cajun cream. Add crab +$10.</p></div>
      <div class="item"><div class="row">SHRIMP &amp; GRITS<span class="lead"></span><span class="price"><sup>$</sup>28</span></div><p class="desc">Sautéed shrimp, onions, peppers in cream over cheesy grits.</p></div>
      <div class="item"><div class="row">OXTAILS<span class="lead"></span><span class="price"><sup>$</sup>40</span></div><p class="desc">Braised oxtails with butter beans, two sides.</p></div>
      <div class="item"><div class="row">CARIBBEAN LAMB CHOPS<span class="lead"></span><span class="price"><sup>$</sup>45</span></div><p class="desc">Lamb chops topped with sweet caribbean glaze, two sides.</p></div>
      <div class="item"><div class="row">LOADED CREOLE PASTA<span class="lead"></span><span class="price"><sup>$</sup>50</span></div><p class="desc">Shrimp, lump crab and crab leg over creamy cajun linguine.</p></div>
      <div class="item"><div class="row">2 BROILED CRAB CAKES<span class="lead"></span><span class="price"><sup>$</sup>MKT</span></div><p class="desc">Two broiled lump crab cakes with two sides.</p></div>
      <div class="item"><div class="row">RED SNAPPER<span class="lead"></span><span class="price"><sup>$</sup>MKT</span></div><p class="desc">Fried or roasted snapper with jambalaya stew sauce, two sides.</p></div>
    </div>
  </div>
  <div class="note" style="left:561px;top:888px;width:210px;height:34px;padding:4px 8px;text-align:center;font-size:7px">Please read menu descriptions carefully and be sure about what you are ordering. All checks will have 20% gratuity added. All parties 4+ will be on one check.</div>

  <div class="band__title" style="top:937px;font-size:24px">SIDES</div>
  <div class="sides">
    <div class="sides__col">CHEESY GRITS <sup>$4</sup><br>SAUTÉED SPINACH <sup>$5</sup><br>SEASONED FRIES <sup>$5</sup><br>FRIED RICE <sup>$6</sup><br>GARLIC MASHED POTATOES <sup>$6</sup></div>
    <div class="sides__col">CORN-SUCCOTASH <sup>$6</sup><br>CORNBREAD <sup>$6</sup><br>SPINACH <sup>$7</sup><br>SWEET POTATOES <sup>$7</sup><br>FIVE CHEESE MAC <sup>$8</sup></div>
    <div class="sides__col" style="line-height:1.45">COLLARD GREENS WITH<br>SMOKED TURKEY <sup>$8</sup><br>BROCCOLINI <sup>$9</sup><br>CAJUN CRAB FRIES <sup>$15</sup><br>SEAFOOD FRIED RICE <sup>$15</sup></div>
  </div>
  <div class="footer" style="top:1075px;font-size:10px">18% service charge on small parties of <b>4</b><br><b>20%</b> service charge large parties of <b>6</b> or more.</div>
  <div class="footer" style="top:1105px;font-size:8.2px">Please alert your server if you have any food allergies. Consuming raw or undercooked meats, poultry, seafood, shellfish or eggs may increase your risk of foodborne illness.</div>
</section>

<!-- DRINKS PAGE -->
<section class="page page--drinks">
  <div class="brand"><span class="brand__dot"></span><span class="brand__name">Miss Della's</span></div>
  <div class="header__rule"></div>
  <div class="hours">
    <h3>HAPPY HOUR FOOD &amp; DRINKS</h3>
    <p>MONDAY TO FRIDAY 3:00PM-6:00PM</p>
    <p class="small">Bar seats and high top tables by bar ONLY</p>
    <h3>BRUNCH</h3>
    <p>SATURDAY &amp; SUNDAY 10:00AM-4:00PM</p>
  </div>
  <div class="band" style="top:172px"></div>

  <div class="col" style="left:45px;top:222px;width:195px;height:400px">
    <h2 class="heading">BEVERAGES</h2>
    <span class="flourish" role="img" aria-label="Scroll flourish divider" style="width:150px"></span>
    <div class="list" style="margin-top:28px">
      <div class="item"><div class="row">SOFT DRINKS<span class="lead"></span><span class="price"><sup>$</sup>4 (free refills)</span></div><p class="desc">Cola | Lemon-lime soda | Orange Juice | Ginger Ale | Pineapple Juice | Cranberry Juice</p></div>
      <div class="item"><div class="row">GINGER BEER<span class="lead"></span><span class="price"><sup>$</sup>4</span></div></div>
      <div class="item"><div class="row">FRESH SQUEEZE LEMONADE<span class="lead"></span><span class="price"><sup>$</sup>5</span></div><p class="desc">Peach, Strawberry, Passion-fruit, Blackberry, Blueberry</p></div>
      <div class="item"><div class="row">ICED TEA<span class="lead"></span><span class="price"><sup>$</sup>5</span></div><p class="desc">Peach, Strawberry, Passion-fruit, Blackberry, Blueberry</p></div>
      <div class="item"><div class="row">STILL SPRING WATER<span class="lead"></span><span class="price"><sup>$</sup>5</span></div></div>
      <div class="item"><div class="row">SPARKLING MINERAL WATER<span class="lead"></span><span class="price"><sup>$</sup>5</span></div></div>
      <div class="item"><div class="row">BLUEBERRY FIZZ<span class="lead"></span><span class="price"><sup>$</sup>12</span></div><p class="desc">Blueberry, Lime, Ginger beer</p></div>
      <div class="item"><div class="row">PINEAPPLE PUNCH<span class="lead"></span><span class="price"><sup>$</sup>12</span></div><p class="desc">Pineapple juice, Orange juice, Peach syrup, Fresh lime juice</p></div>
    </div>
  </div>

  <div class="col" style="left:45px;top:665px;width:170px;height:330px">
    <h2 class="heading">SPIRITS</h2>
    <span class="flourish" role="img" aria-label="Scroll flourish divider" style="width:150px"></span>
    <div class="list" style="margin-top:24px">
      <div class="item"><div class="row">BOURBON &amp; WHISKEY</div><p class="desc">Oak Barrel, Copper Still, Red Hollow, Green Isle, King's Grain, Hollow Creek, Old Pike</p></div>
      <div class="item"><div class="row">SCOTCH</div><p class="desc">Highland Crest Black, Glen Arden, Glen Arden 12</p></div>
      <div class="item"><div class="row">VODKA</div><p class="desc">Ridgeline Vodka, Frostline, White Heron, Pale Birch</p></div>
      <div class="item"><div class="row">GIN</div><p class="desc">Juniper Row, Blue Lantern, Crown Botanic</p></div>
      <div class="item"><div class="row">TEQUILA</div><p class="desc">Casa Luna Blanco, Casa Luna Reposado, Agave Real, Sol Dorado, Sol Dorado Añejo</p></div>
      <div class="item"><div class="row">RUM</div><p class="desc">Isla Blanca Silver, Harbor Spiced, Dark Reef Rum</p></div>
    </div>
  </div>

  <div class="col" style="left:292px;top:222px;width:190px;height:810px">
    <h2 class="heading">SPECIALTY<br>COCKTAILS</h2>
    <span class="flourish" role="img" aria-label="Scroll flourish divider" style="width:160px"></span>
    <div class="list" style="margin-top:18px">
      <div class="item"><div class="row">PINK LADY<span class="lead"></span><span class="price"><sup>$</sup>15</span></div><p class="desc">Tequila, Orange liqueur, Lime juice, Strawberry-kiwi agave.</p></div>
      <div class="item"><div class="row">BLACKBERRY FRENCH<span class="lead"></span><span class="price"><sup>$</sup>15</span></div><p class="desc">Botanic gin, Champagne, Lemonade, White flowers.</p></div>
      <div class="item"><div class="row">SECRETS<span class="lead"></span><span class="price"><sup>$</sup>15</span></div><p class="desc">Secret blend of 3 rums, Tropical punch, Fresh lime.</p></div>
      <div class="item"><div class="row">PEACH PLEASE<span class="lead"></span><span class="price"><sup>$</sup>16</span></div><p class="desc">Ridgeline Vodka, Champagne, Peach nectar, orange juice.</p></div>
      <div class="item"><div class="row">TOASTED MARSHMALLOW<br>ESPRESSO MARTINI<span class="lead"></span><span class="price"><sup>$</sup>16</span></div><p class="desc">Ridgeline Vodka, Espresso liqueur, Irish cream, Toasted marshmallows.</p></div>
      <div class="item"><div class="row">MISS DELLA'S HURRICANE<span class="lead"></span><span class="price"><sup>$</sup>16</span></div><p class="desc">Dark rum, Light rum, Passionfruit, Lime juice, Orange juice, Grenadine.</p></div>
      <div class="item"><div class="row">TSUNAMI<span class="lead"></span><span class="price"><sup>$</sup>16</span></div><p class="desc">Blanco tequila, Pineapple, Orange, Passionfruit, Blue curacao, dark tequila.</p></div>
      <div class="item"><div class="row">MISKIRI VIII<span class="lead"></span><span class="price"><sup>$</sup>17</span></div><p class="desc">Tequila, Orange liqueur, Blackberry, Pineapple, Cranberry, Lemon juice.</p></div>
      <div class="item"><div class="row">LOUISIANA TEA<span class="lead"></span><span class="price"><sup>$</sup>17</span></div><p class="desc">Hollow Creek, Honey mint syrup, Fresh lemonade.</p></div>
      <div class="item"><div class="row">DELLA'S PASSION<span class="lead"></span><span class="price"><sup>$</sup>18</span></div><p class="desc">Belmont, Orange liqueur, Lemon juice, Passionfruit.</p></div>
      <div class="item"><div class="row">PINEAPPLE-GRIA<span class="lead"></span><span class="price"><sup>$</sup>18</span></div><p class="desc">White sparkling wine, Rum, Pineapple punch.</p></div>
      <div class="item"><div class="row">SMOKED IN FASHION<span class="lead"></span><span class="price"><sup>$</sup>18</span></div><p class="desc">Hollow Creek, Cubed sugar, Black cherry, Orange and Cherry bitters.</p></div>
      <div class="item"><div class="row">SMOKED TEQUILA OLD FASHION<span class="lead"></span><span class="price"><sup>$</sup>18</span></div><p class="desc">Aged tequila, Orange liqueur, Agave nectar, Peach bitters, Orange peel.</p></div>
      <div class="item"><div class="row">BECKY SANGRIA<span class="lead"></span><span class="price"><sup>$</sup>18</span></div><p class="desc">Red wine blend, Belmont, Tropical fruit punch, Frozen popsicle.</p></div>
      <div class="item"><div class="row">CREOLE ISLAND<span class="lead"></span><span class="price"><sup>$</sup>19</span></div><p class="desc">Belmont, Orange liqueur, Tropical punch</p></div>
      <div class="item"><div class="row">MARGARITA OR LEMON DROP FLIGHT<span class="lead"></span><span class="price"><sup>$</sup>20</span></div><p class="desc">Signature margarita and lemon drops $20</p></div>
    </div>
  </div>

  <div class="frame" style="left:550px;top:225px;width:222px;height:277px;padding:22px 20px 20px">
    <h2 class="heading">LUNCH DRINK<br>SPECIALS</h2>
    <span class="flourish" role="img" aria-label="Scroll flourish divider" style="width:170px;margin:4px auto 0"></span>
    <div class="list" style="height:155px;margin-top:18px">
      <div class="item"><div class="row">GLASS OF HOUSE WINE<br>(RED OR WHITE)<span class="lead"></span><span class="price"><sup>$</sup>6</span></div></div>
      <div class="item"><div class="row">MISS DELLA'S HURRICANE<span class="lead"></span><span class="price"><sup>$</sup>7</span></div><p class="desc">Peach, Strawberry, Passion-fruit, Blackberry, Blueberry</p></div>
      <div class="item"><div class="row">SIGNATURE MARGARITA<span class="lead"></span><span class="price"><sup>$</sup>7</span></div><p class="desc">Tequila, Orange liqueur, Add a flavor $1</p></div>
      <div class="item"><div class="row">CLASSIC LEMON DROP<span class="lead"></span><span class="price"><sup>$</sup>7</span></div><p class="desc">Vodka, Lemon juice, Simple syrup, Sugar rim 7</p></div>
    </div>
  </div>

  <div class="frame" style="left:550px;top:540px;width:222px;height:310px;padding:20px 18px 20px">
    <h2 class="heading" style="font-size:24px;white-space:nowrap;margin:0 -12px">WINE &amp; BUBBLY</h2>
    <span class="flourish" role="img" aria-label="Scroll flourish divider" style="width:110px;margin:4px auto 0"></span>
    <div class="list" style="height:195px;margin-top:18px">
      <div class="item"><div class="row">REDS<span class="lead"></span><span class="price"><sup>$</sup>6</span></div><p class="desc" style="display:grid;grid-template-columns:45px 1fr">Cabernet<span>Pinot Noir</span>Merlot<span>Sweet Red Blend</span></p></div>
      <div class="item"><div class="row">WHITE<span class="lead"></span><span class="price"><sup>$</sup>6</span></div><p class="desc">Moscato, Pinot Grigio, Sauvignon Blanc, Chardonnay</p></div>
      <div class="item"><div class="row">MESA RIDGE CHARDONNAY<span class="lead"></span><span class="price"><sup>$</sup>7</span></div></div>
      <div class="item"><div class="row">MESA RIDGE CABERNET<span class="lead"></span><span class="price"><sup>$</sup>7</span></div></div>
      <div class="item"><div class="row">BARE VINE MOSCATO<span class="lead"></span><span class="price"><sup>$</sup>7</span></div></div>
      <div class="item"><div class="row">ALDER HILL CHARDONNAY<span class="lead"></span><span class="price"><sup>$</sup>10</span></div></div>
      <div class="item"><div class="row">ALDER HILL CABERNET<span class="lead"></span><span class="price"><sup>$</sup>10</span></div></div>
    </div>
  </div>

  <div class="ornament" role="img" aria-label="Gold scroll ornament" style="left:630px;top:880px;width:56px;height:95px;border-radius:28px 28px 40% 40%"></div>
  <div class="ornament" role="img" aria-label="Gold scroll border flourish" style="left:175px;top:1050px;width:470px;height:8px;border-radius:4px"></div>

  <div class="footer" style="top:1080px;font-size:9px">Please alert your server if you have any food allergies.<br>Consuming raw or undercooked meats, poultry, seafood, shellfish or eggs may increase your risk of foodborne illness</div>
</section>

</body>
</html>
```